QRV Advisors needs a web site

We need a web site for www.qrvadvisors-example.com. QRV is a mergers and acquisition consulting company that focuses our buyer and seller services on logistics companies. We help put companies together, and help with legal and financial due diligence. We want the web site to express our service and show the logistics components. We want personalized images versus pictures of trucks and airplanes.

Our new logo uses Burgandy and grey colors. Image attached. We are not in to bold, big letters...classy, artistic, low key preferred. Confidentiality, experience, professional are what we want to express on the site.

All we expect for the first part of this project is a home page, and one subpage.  We are budgeting other funds for the technical aspects of the web site

Reason: All that I'm seeing so far is trucks, forklifts and planes. We are a legal mergers and acquisitions firm that focus on logistics. I like some of the images to say logistics, but really want it say legal, financial, and putting companies together. Will pay extra for the sub page if someone can impress us with a home page.

Reason: Swamped with another project at the moment...will work on this over the weekend and provide designer feedback and select final design by Tuesday

```html
<!DOCTYPE html>
<html lang="en">
<head>
<meta charset="utf-8">
<title>QRV Advisors — Home</title>
<link rel="stylesheet" href="https://fonts.googleapis.com/css2?family=Rambla:wght@400;700&family=Ubuntu:wght@400;500;700&display=swap">
<style>
:root{
  --burgundy:#a5093a;
  --burgundy-dark:#8a0730;
  --slate:#56575b;
  --slate-dark:#4a4b4f;
  --ink:#333436;
  --text:#4a4a4a;
  --page:#f1f1f2;
  --white:#ffffff;
  --footer:#2f2f31;
  --footer-line:#4a4a4c;
}
*{margin:0;padding:0;box-sizing:border-box}
html,body{width:1028px;height:1200px;overflow:hidden}
body{position:relative;background:var(--page);font-family:"Ubuntu",sans-serif;color:var(--text)}
.abs{position:absolute}

/* header */
.topbar{left:0;top:0;width:1028px;height:6px;background:#666}
.header{left:0;top:6px;width:1028px;height:119px;background:linear-gradient(#f7f7f7,#e2e2e3);border-bottom:1px solid #c9c9c9}
.brand{left:120px;top:50px;display:flex;align-items:center;gap:10px}
.brand-mark{width:16px;height:16px;background:var(--burgundy)}
.brand-name{font-family:"Ubuntu",sans-serif;font-weight:500;font-size:30px;color:var(--slate);letter-spacing:.5px}
.social-top{left:648px;top:24px;display:flex;gap:10px}
.dot{width:28px;height:28px;border-radius:50%;background:#5d5e62}
.call{left:776px;top:20px;display:flex;align-items:center;gap:6px}
.call-text small{display:block;font-size:10px;color:#444}
.call-text strong{display:block;font-weight:400;font-size:16px;color:#333}
.nav{left:380px;top:75px;display:flex;gap:14px}
.nav a{display:block;padding:7px 3px;border-top:1px solid #b5b5b5;border-bottom:1px solid #b5b5b5;font-size:9.3px;color:#444;text-decoration:none;text-transform:uppercase;white-space:nowrap;position:relative}
.nav a.active{font-weight:700;color:#333}
.nav a.active::before{content:"";position:absolute;left:50%;top:-1px;margin-left:-4px;border:4px solid transparent;border-top-color:#333}

/* hero */
.hero{left:0;top:126px;width:1028px;height:376px;background:radial-gradient(ellipse at 52% 35%,#c9b9ad 0%,#8c8c90 40%,#6a6d74 100%)}
.hero-grid{left:0;top:126px;width:1028px;height:376px}
.hero-arrow{top:300px}
.caption{left:118px;top:422px;width:792px;height:80px;background:rgba(255,255,255,.78);font-family:"Rambla",sans-serif;font-weight:700;font-size:24.5px;color:#4d4d4f;text-align:center;line-height:32px;padding-top:9px}

/* services */
.section-title{left:0;top:515px;width:1028px;text-align:center;font-family:"Rambla",sans-serif;font-size:24px;color:var(--burgundy)}
.title-rule{top:530px;height:1px;background:#b8b8b8}
.service{top:563px;width:237px;height:148px;background:var(--white);box-shadow:0 1px 3px rgba(0,0,0,.2)}
.service-head{height:91px;background:var(--slate);position:relative}
.service-head.accent{background:var(--burgundy)}
.service-head h3{position:absolute;left:11px;bottom:6px;font-family:"Rambla",sans-serif;font-weight:400;font-size:20.5px;line-height:23px;color:var(--white)}
.service-head svg{position:absolute;right:8px;bottom:0}
.service p{padding:4px 9px;font-size:10.2px;line-height:14.6px;color:#555}
.divider-shadow{left:20px;top:724px;width:988px;height:10px;background:radial-gradient(ellipse at center,rgba(0,0,0,.12),rgba(0,0,0,0) 70%)}

/* info panels */
.panel{top:760px;height:230px;background:var(--white);border-radius:4px;box-shadow:0 4px 6px rgba(0,0,0,.15);border:1px solid #ddd}
.panel-head{position:absolute;left:-5px;right:-5px;top:11px;height:31px;background:var(--slate);display:flex;align-items:center;gap:10px;padding-left:12px;color:var(--white);font-size:17px;letter-spacing:.4px}
.about-photo{position:absolute;left:9px;top:58px;width:228px;height:88px;background:linear-gradient(110deg,#e9ecf1 0%,#b8c3d0 45%,#2e3a52 70%,#c9ccd4 100%)}
.about-text{position:absolute;left:14px;top:151px;width:220px;font-size:9.5px;line-height:12.4px;color:#555;letter-spacing:.3px}
.more{position:absolute;right:9px;bottom:13px;font-size:9.5px;font-weight:500;color:#444}
.news{position:absolute;left:10px;top:58px;width:230px}
.news-item{display:flex;gap:10px;margin-bottom:10px;height:38px}
.date{width:31px;flex:none;text-align:center;box-shadow:0 1px 2px rgba(0,0,0,.25)}
.date b{display:block;background:var(--burgundy);color:var(--white);font-size:11px;line-height:15px}
.date i{display:block;font-style:normal;font-weight:700;font-size:10px;line-height:15px;color:#333;background:#fff}
.news-item p{font-size:9.3px;line-height:12.2px;color:#555}
.news-item p strong{color:#222}
.field{position:absolute;left:11px;width:225px;height:20px;border:1px solid #bbb;border-radius:3px;font-size:9.8px;color:#666;padding:3px 8px;background:#fff}
.submit{position:absolute;left:13px;top:201px;width:55px;height:19px;background:var(--burgundy);color:var(--white);font-weight:700;font-size:12px;text-align:center;line-height:19px}

/* footer */
.footer{left:0;top:1018px;width:1028px;height:182px;background:var(--footer);border-top:3px solid var(--burgundy)}
.foot-title{top:1034px;font-size:15.5px;color:#eee}
.foot-rule{height:0;border-top:1px dashed var(--footer-line)}
.vline{width:1px;background:var(--footer-line)}
.links{left:118px;top:1065px;list-style:none}
.links li{font-size:10px;line-height:14.3px;color:#eee;padding-left:13px;position:relative}
.links li::before{content:"›";position:absolute;left:0;top:-1px;color:#aaa}
.map{left:288px;top:1068px;width:184px;height:80px;background:linear-gradient(150deg,#efeee9,#dcdad3);border:3px solid #f4f4f4}
.contact-row{left:480px;display:flex;align-items:flex-start;gap:9px;font-size:10.3px;line-height:15px;color:#eee}
.foot-brand{left:730px;top:1038px;width:178px;text-align:center;font-family:"Ubuntu",sans-serif;font-weight:500;font-size:52px;color:#fff;letter-spacing:4px}
.social-foot{left:764px;top:1116px;display:flex;gap:10px}
.social-foot .dot{width:31px;height:31px;border-radius:6px;background:#58595d}
.copyright{left:0;top:1168px;width:1028px;text-align:center;font-size:12px;color:#eee}
</style>
</head>
<body>

<div class="abs topbar"></div>
<header class="abs header"></header>

<div class="abs brand">
  <span class="brand-mark"></span>
  <span class="brand-name">QRV Advisors</span>
</div>

<div class="abs social-top" aria-label="Social links">
  <span class="dot"></span><span class="dot"></span><span class="dot"></span>
</div>

<div class="abs call">
  <svg width="28" height="28" viewBox="0 0 28 28"><circle cx="14" cy="14" r="12.5" fill="none" stroke="#a5093a" stroke-width="1.6"/><path d="M10 8c1.5-1 2.5 1 3 2.5.3 1-1.3 1.4-1 2.6.5 1.6 1.5 3 2.8 3.7 1 .5 1.6-1 2.6-.6 1.4.6 3.2 1.8 2 3-1.6 1.7-4 .9-6-.6-2.3-1.8-4-4.6-4.3-7-.2-1.6.1-3 .9-3.6z" fill="#a5093a"/></svg>
  <div class="call-text"><small>Call Us Today</small><strong>555 014 2290</strong></div>
</div>

<nav class="abs nav">
  <a class="active" href="#">Home</a>
  <a href="#">About Us</a>
  <a href="#">Buyer Services</a>
  <a href="#">Seller Services</a>
  <a href="#">News &amp; Events</a>
  <a href="#" style="text-transform:none">FAQ's</a>
  <a href="#">Contact</a>
</nav>

<div class="abs hero" role="img" aria-label="Professional touching a glowing financial growth chart on a transparent screen"></div>
<svg class="abs hero-grid" width="1028" height="376" viewBox="0 0 1028 376">
  <g stroke="#fff" stroke-width="3" stroke-dasharray="4 4" fill="none" opacity=".9">
    <line x1="4" y1="160" x2="980" y2="160"/>
    <line x1="4" y1="284" x2="980" y2="284"/>
    <line x1="4" y1="341" x2="980" y2="341"/>
    <line x1="980" y1="112" x2="980" y2="360" stroke-dasharray="4 10"/>
  </g>
  <polyline points="390,320 395,240 410,270 425,300 440,250 470,275 500,240 525,270 540,300 560,260 585,230 600,165 625,245 640,300 655,250 680,260 700,250 720,210 740,245 760,250 790,250" fill="none" stroke="#e0506a" stroke-width="1.5"/>
  <path d="M92 318l12-14M92 318l12 14" stroke="#111" stroke-width="5" fill="none"/>
  <path d="M938 318l-12-14M938 318l-12 14" stroke="#111" stroke-width="5" fill="none"/>
</svg>
<div class="abs caption">QRV Services Are Offered By Industry Executives With Extensive<br>M&amp;A Experience</div>

<h2 class="abs section-title" style="font-weight:400">Our Services</h2>
<div class="abs title-rule" style="left:200px;width:222px"></div>
<div class="abs title-rule" style="left:617px;width:222px"></div>

<article class="abs service" style="left:119px">
  <div class="service-head accent">
    <h3>Business<br>Planning</h3>
    <svg width="62" height="62" viewBox="0 0 62 62"><rect x="8" y="4" width="38" height="56" rx="2" fill="none" stroke="#fff" stroke-width="3"/><g stroke="#fff" stroke-width="3"><line x1="14" y1="14" x2="40" y2="14"/><line x1="14" y1="22" x2="40" y2="22"/><line x1="14" y1="30" x2="40" y2="30"/><line x1="14" y1="38" x2="30" y2="38"/></g><path d="M30 46l8 8 18-18" stroke="#fff" stroke-width="4" fill="none"/></svg>
  </div>
  <p>Lorem ipsum dolor sit amet, consectetuer eadi pis elit, sed diam nonummy nibh euismod tinc idunt ut laoreeio dolore magna aliquam erate</p>
</article>
<article class="abs service" style="left:394px">
  <div class="service-head">
    <h3>Mergers &amp;<br>Acquisition</h3>
    <svg width="70" height="50" viewBox="0 0 70 50"><path d="M4 20l14-10 14 6 10-6 24 10-6 14-20 12-6-4-6 2-6-6-6 0-8-8z" fill="#fff"/></svg>
  </div>
  <p>Lorem ipsum dolor sit amet, consectetuer eadi pis elit, sed diam nonummy nibh euismod tinc idunt ut laoreeio dolore magna aliquam erate</p>
</article>
<article class="abs service" style="left:670px">
  <div class="service-head">
    <h3>Advisory<br>Services</h3>
    <svg width="52" height="52" viewBox="0 0 52 52"><circle cx="16" cy="22" r="7" fill="#fff"/><path d="M2 52c0-12 6-18 14-18s14 6 14 18z" fill="#fff"/><rect x="24" y="2" width="26" height="18" rx="2" fill="none" stroke="#fff" stroke-width="2.5"/><path d="M30 20l-4 7 9-7" fill="#fff"/><g stroke="#fff" stroke-width="2"><line x1="29" y1="8" x2="45" y2="8"/><line x1="29" y1="14" x2="42" y2="14"/></g></svg>
  </div>
  <p>Lorem ipsum dolor sit amet, consectetuer eadi pis elit, sed diam nonummy nibh euismod tinc idunt ut laoreeio dolore magna aliquam erate</p>
</article>

<div class="abs divider-shadow"></div>

<section class="abs panel" style="left:123px;width:243px">
  <div class="panel-head">
    <svg width="20" height="16" viewBox="0 0 20 16" fill="#fff"><circle cx="10" cy="4" r="3"/><circle cx="4" cy="6" r="2.4"/><circle cx="16" cy="6" r="2.4"/><path d="M5 16c0-5 2-7 5-7s5 2 5 7z"/><path d="M0 14c0-3 1.5-5 4-5 1 0 1.6.3 2 .8-1 1.2-1.4 2.6-1.5 4.2z"/><path d="M20 14c0-3-1.5-5-4-5-1 0-1.6.3-2 .8 1 1.2 1.4 2.6 1.5 4.2z"/></svg>
    ABOUT QRV
  </div>
  <div class="about-photo" role="img" aria-label="Business team in conversation"></div>
  <p class="about-text">QRV assists business owners within the logistics industry to implement growth and exit strategies. We offer business planning and merger and acquisition (M&amp;A) advisory services.</p>
  <span class="more">Read More »</span>
</section>

<section class="abs panel" style="left:394px;width:243px">
  <div class="panel-head">
    <svg width="16" height="16" viewBox="0 0 16 16"><rect x="1" y="2" width="14" height="13" fill="none" stroke="#fff" stroke-width="1.5"/><rect x="1" y="2" width="14" height="3" fill="#fff"/><g fill="#fff"><rect x="3" y="7" width="2" height="2"/><rect x="7" y="7" width="2" height="2"/><rect x="11" y="7" width="2" height="2"/><rect x="3" y="11" width="2" height="2"/><rect x="7" y="11" width="2" height="2"/><rect x="11" y="11" width="2" height="2"/></g></svg>
    NEWS &amp; EVENTS
  </div>
  <div class="news">
    <div class="news-item"><div class="date"><b>Apr</b><i>02</i></div><p><strong>Lorem ipsum dolor sit amet, consectetue</strong> eadi pis elit, sed diam nonummy nibherini euismod tinc idunt ut laoreeio.</p></div>
    <div class="news-item"><div class="date"><b>Apr</b><i>03</i></div><p><strong>Lorem ipsum dolor sit amet, consectetue</strong> eadi pis elit, sed diam nonummy nibherini euismod tinc idunt ut laoreeio.</p></div>
    <div class="news-item"><div class="date"><b>Apr</b><i>04</i></div><p><strong>Lorem ipsum dolor sit amet, consectetue</strong> eadi pis elit, sed diam nonummy nibherini euismod tinc idunt ut laoreeio.</p></div>
  </div>
  <span class="more">Read More »</span>
</section>

<section class="abs panel" style="left:665px;width:243px">
  <div class="panel-head">
    <svg width="16" height="16" viewBox="0 0 16 16" fill="none" stroke="#fff" stroke-width="1.6"><path d="M10 2H2v13h11V8"/><path d="M6 11l1-3 7-7 2 2-7 7z" fill="#fff"/></svg>
    QUICK CONTACT
  </div>
  <div class="field" style="top:58px">Name</div>
  <div class="field" style="top:86px">Email</div>
  <div class="field" style="top:115px">Phone</div>
  <div class="field" style="top:143px;height:53px">Message</div>
  <div class="submit">Submit</div>
</section>

<footer class="abs footer"></footer>
<h4 class="abs foot-title" style="left:118px;font-weight:400">Quick Links</h4>
<div class="abs foot-rule" style="left:118px;top:1059px;width:104px"></div>
<ul class="abs links">
  <li>Home</li><li>About Us</li><li>Consulting Services</li><li>News &amp; Events</li><li>FAQ's</li><li>Contact Us</li>
</ul>
<div class="abs vline" style="left:254px;top:1038px;height:112px"></div>

<h4 class="abs foot-title" style="left:288px;font-weight:400">Contact Us</h4>
<div class="abs foot-rule" style="left:288px;top:1059px;width:376px"></div>
<div class="abs map" role="img" aria-label="Street map showing office location"></div>

<div class="abs contact-row" style="top:1068px">
  <svg width="16" height="16" viewBox="0 0 16 16" fill="#eee"><path d="M8 1l7 7h-2v7H9v-4H7v4H3V8H1z"/></svg>
  <span>Lorem ipsum dolor sit amet, conse<br>adipiscing elit, sed diam nonummy.</span>
</div>
<div class="abs contact-row" style="top:1104px">
  <svg width="16" height="16" viewBox="0 0 16 16"><circle cx="8" cy="8" r="7" fill="none" stroke="#eee" stroke-width="1.3"/><path d="M6 4c1-.5 1.5.6 1.7 1.4.1.6-.7.8-.6 1.5.3.9.9 1.7 1.6 2.1.6.3.9-.6 1.5-.3.8.3 1.8 1 1.1 1.7-.9 1-2.3.5-3.4-.4C6.600 9 5.600 7.400 5.500 6c-.1-.9 0-1.700.5-2z" fill="#eee"/></svg>
  <span>555.014.2290</span>
</div>
<div class="abs contact-row" style="top:1130px">
  <span style="font-size:15px;line-height:15px;font-weight:500">@</span>
  <span>info@qrvadvisors-example.com</span>
</div>

<div class="abs vline" style="left:700px;top:1038px;height:112px"></div>
<div class="abs foot-brand">QRV</div>
<div class="abs social-foot" aria-label="Social links">
  <span class="dot"></span><span class="dot"></span><span class="dot"></span>
</div>

<p class="abs copyright">© 2014 qrvadvisors-example.com.&nbsp; All Rights Reserved .</p>

</body>
</html>
```